Website Redesign for Non-Profit Ministry & Church

NOTE: Please do not contact me privately — all private inquiries will be ignored.

Individuals seeking spiritual healing, community connection, ministry support and journal-based encounters.

Description of What’s Needed

We need a clean, fresh, inviting website that encourages engagement and connection. The site should feel warm and accessible, draw people in, and clearly present who we are, what we offer, and how visitors can participate. The layout should be straightforward, with well-structured pages (no overlapping objects, minimal layering complexity) and easy to navigate. Use only Google Fonts. All stock photos must be sourced from royalty-free sites and include proper attribution. We will not include a search feature.

Pages to Create
1. Home Page – impactful hero area, clear call-to-action, visual story of ministry, giving/gathering invitation.
2. About Us – vision, mission, leadership, testimonies, history.
3. Meetings & Events – upcoming gatherings, schedule, how to attend, sign-up or interest form.
4. Encounter: “Lanterns by the River” (book) – dedicated page for the book, overview, purchase link or details, journal prompts, imagery.
5. Healing Rooms / Ministry – explain ministry offerings, invite participation, testimonials or case-studies.
6. Live Stream & Links Page – page listing links for YouTube live stream, other platforms, archive links; simple layout.

Colour & Branding

Use colours that blend with our existing logo (attached). The palette should feel contemporary, welcoming, and aligned with ministry themes of restoration, healing and love. Ensure text, button and link colours maintain good contrast for accessibility.

Existing Content & Reference

Please gather available content from our current website in the attachment here for text, images and structure for reuse.

Imagery Guidelines

– Use original photos from our Facebook page or Google Location listing for building or people images when available.
– If generic images are used, ensure they depict appropriate ministry-related buildings or people (community, warm gathering) — avoid generic unrelated stock imagery.
– All photos must be royalty-free or have proper licensing and attribution.
– No overlapping objects or visual clutter; clean layouts with defined sections.

Additional Notes

– Integration: We currently utilise MailChimp for email communication; the design should include a connection/invite to subscribe (via MailChimp) but no blog page is required at this time.
– Payment/Giving: We accept PayPal and already have a giving portal; include clear donation/give buttons or calls-to-action linking to existing giving systems.
– No search function to be included.
– Layouts should avoid complex layering or overlapping elements—designers should work with distinct content blocks, clear visual hierarchy, and straightforward mobile-friendly structure.

Target Market(s)

Industry/Entity Type

Church/Religious institution

Number of Pages Required

5+ page

Requirements
Should not have
• search bar

```html
<!DOCTYPE html>
<html lang="en">
<head>
<meta charset="utf-8">
<title>Whole &amp; Beloved — Experience Healing, Restoration &amp; Community</title>
<link href="https://fonts.googleapis.com/css2?family=Roboto:wght@400;500;700&display=swap" rel="stylesheet">
<style>
:root{
  --teal:#07a69a;
  --teal-dark:#05897f;
  --forest:#0c5a30;
  --purple:#3b1a6b;
  --ink:#111111;
  --text:#2a2a2a;
  --muted:#444;
  --white:#ffffff;
}
*{box-sizing:border-box;margin:0;padding:0}
html,body{width:1200px;height:3236px;overflow:hidden}
body{font-family:'Roboto',sans-serif;color:var(--ink);background:var(--white);position:relative}
.abs{position:absolute}
a{text-decoration:none;color:inherit}

.btn{position:absolute;display:flex;align-items:center;justify-content:center;font-weight:700;font-size:13px;color:var(--white);border-radius:6px;text-transform:uppercase;letter-spacing:.1px}
.btn--teal{background:var(--teal)}
.btn--black{background:#000}
.btn--forest{background:var(--forest)}
.btn--purple{background:var(--purple)}

/* Hero */
.hero{position:absolute;left:0;top:0;width:1200px;height:800px;
  background:linear-gradient(180deg,#a8c3cc 0%,#c9d8dc 30%,#dcd9cf 48%,#ecc9a0 58%,#e7a46a 64%,#8a7a70 70%,#5a5a5e 82%,#3e3e42 100%)}
.brand{display:flex;align-items:center;gap:10px}
.brand__dot{width:14px;height:14px;border-radius:50%;background:var(--teal)}
.brand__name{font-weight:700;font-size:21px;color:var(--teal-dark);line-height:1.05}
.nav{position:absolute;display:flex;align-items:center;font-size:13.4px;font-weight:500;color:var(--ink);white-space:nowrap}
.nav span.sep{margin:0 10px}
.hero__title{left:142px;top:262px;font-size:40px;font-weight:700;line-height:51px}
.hero__title .lead{color:var(--forest)}
.hero__copy{left:143px;top:388px;font-size:15px;font-weight:500;line-height:27px;color:#111}

/* Story + invite background */
.story{position:absolute;left:0;top:800px;width:1200px;height:1299px;
  background:linear-gradient(180deg,#e4e1db 0%,#ece8e2 50%,#f1efea 100%)}
.section-title{position:absolute;left:0;width:1200px;text-align:center;font-size:40px;font-weight:700;color:var(--ink)}
.card{position:absolute;width:434px;height:299px;background:var(--white);border-radius:4px;padding:30px 30px 0 30px}
.card--outlined{border:1px solid #cfcfcf}
.card__icon{width:84px;height:84px;border-radius:50%;background:var(--teal);display:flex;align-items:center;justify-content:center;margin-left:4px}
.card__title{margin-top:26px;font-size:19px;font-weight:500;color:var(--ink)}
.card__text{margin-top:20px;font-size:13px;line-height:26px;color:var(--muted);width:370px}

.invite__text{left:280px;width:640px;top:1887px;text-align:center;font-size:15px;line-height:27px;color:var(--text)}

/* Photo + subscribe */
.photo{position:absolute;left:0;top:2099px;width:1200px;height:673px;
  background:radial-gradient(ellipse at 55% 40%,#e8c89a 0%,#c89a5e 40%,#a87a3e 70%,#8a6330 100%)}
.subscribe{position:absolute;left:149px;top:2611px;width:917px;height:297px;background:var(--teal);border-radius:16px}
.subscribe__title{position:absolute;left:0;width:100%;top:52px;text-align:center;color:var(--white);font-size:40px;font-weight:700}
.subscribe__text{position:absolute;left:0;width:100%;top:128px;text-align:center;color:var(--white);font-size:15px}
.subscribe__input{position:absolute;left:160px;top:178px;width:437px;height:54px;background:var(--white);border-radius:6px;font-size:15px;color:#666;padding-left:22px;display:flex;align-items:center}
.subscribe__btn{left:606px;top:178px;width:137px;height:54px;font-size:15px}

/* Footer */
.social{position:absolute;width:47px;height:46px;background:var(--teal);border-radius:6px;display:flex;align-items:center;justify-content:center}
.social__mark{width:12px;height:12px;border-radius:50%;background:var(--white)}
.footer__rule{left:108px;top:3125px;width:984px;height:1px;background:#cfcfcf}
.copyright{left:0;width:1200px;top:3155px;text-align:center;font-size:13px;color:var(--text)}
.pageno{right:14px;top:3178px;font-size:13px;color:#555}
</style>
</head>
<body>

<header class="hero" role="img" aria-label="Sunset over a calm sea with a distant shoreline"></header>
<div class="abs brand" style="left:142px;top:28px">
  <span class="brand__dot"></span>
  <span class="brand__name">Whole &amp;<br>Beloved</span>
</div>
<a class="btn btn--teal" style="left:930px;top:8px;width:124px;height:44px">Donate Now</a>
<nav class="nav" style="left:342px;top:73px">
  <a>HOME</a><span class="sep">|</span><a>ABOUT US</a><span class="sep">|</span><a>MEETINGS &amp; EVENTS</a><span class="sep">|</span><a>LANTERNS BY THE RIVER</a><span class="sep">|</span><a>HEALING ROOMS</a><span class="sep">|</span><a>LIVE&nbsp; STREAMING</a>
</nav>
<h1 class="abs hero__title"><span class="lead">Experience Healing,</span><br>Restoration &amp; Community</h1>
<p class="abs hero__copy">Join us on a journey of hope, connection, and spiritual growth.<br>Wherever you are, there’s a place for you here.</p>
<a class="btn btn--teal" style="left:145px;top:476px;width:168px;height:44px">Join a Gathering</a>
<a class="btn btn--black" style="left:319px;top:478px;width:126px;height:45px">Give Today</a>

<section class="story"></section>
<h2 class="section-title" style="top:900px">Our Story</h2>

<article class="card" style="left:144px;top:1018px">
  <div class="card__icon"><svg width="44" height="44" viewBox="0 0 44 44" fill="none" stroke="#fff" stroke-width="1.6" stroke-linecap="round" stroke-linejoin="round"><path d="M6 30h8l8 3h8l8-6"/><path d="M6 36h8l10 3 14-8"/><path d="M22 24V12"/><path d="M22 16c-4-1-6-4-6-8 4 0 6 3 6 8z"/><path d="M22 16c4-1 6-4 6-8-4 0-6 3-6 8z"/></svg></div>
  <h3 class="card__title">Restoration &amp; Healing</h3>
  <p class="card__text">Through our ministries and Healing Rooms, we create safe spaces for restoration, reflection, and renewal.”</p>
</article>
<article class="card card--outlined" style="left:593px;top:1018px">
  <div class="card__icon"><svg width="44" height="44" viewBox="0 0 44 44" fill="none" stroke="#fff" stroke-width="1.6" stroke-linecap="round" stroke-linejoin="round"><circle cx="15" cy="11" r="3"/><circle cx="29" cy="11" r="3"/><path d="M6 26l8-8 6 4 4-4 6 2 8 6"/><path d="M12 28l6 6 4-2 4 2 6-6"/></svg></div>
  <h3 class="card__title">Community &amp; Connection</h3>
  <p class="card__text">Our gatherings and events foster authentic connections, support, and spiritual growth for everyone.”</p>
</article>
<article class="card" style="left:144px;top:1340px">
  <div class="card__icon"><svg width="44" height="44" viewBox="0 0 44 44" fill="none" stroke="#fff" stroke-width="1.6" stroke-linecap="round" stroke-linejoin="round"><path d="M14 38v-7c-4-3-6-7-6-12a13 13 0 0 1 26 0l3 6h-3v5h-5v8"/><circle cx="21" cy="18" r="5"/></svg></div>
  <h3 class="card__title">Lanterns by the River</h3>
  <p class="card__text">Discover transformative journaling practices that guide you toward peace and mindfulness. Explore our book, Lanterns by the River</p>
</article>
<article class="card" style="left:593px;top:1340px">
  <div class="card__icon"><svg width="44" height="44" viewBox="0 0 44 44" fill="none" stroke="#fff" stroke-width="1.6" stroke-linecap="round" stroke-linejoin="round"><rect x="8" y="10" width="28" height="19" rx="1"/><path d="M4 33h36"/><circle cx="19" cy="17" r="3"/><path d="M14 26c1-3 3-4 5-4s4 1 5 4"/><path d="M27 15h6M27 19h6"/></svg></div>
  <h3 class="card__title">Live &amp; Online Engagement</h3>
  <p class="card__text">Join our live streams or catch up with past events—connect from anywhere in the world.</p>
</article>

<h2 class="section-title" style="top:1815px">Invitation to Participate</h2>
<p class="abs invite__text">Your journey with us starts here. Attend a gathering, participate in our Healing Rooms, or join a live stream. There’s a place for everyone.”</p>
<a class="btn btn--teal" style="left:316px;top:1972px;width:168px;height:45px">Find an Event</a>
<a class="btn btn--forest" style="left:495px;top:1972px;width:168px;height:45px">Request Prayer</a>
<a class="btn btn--purple" style="left:674px;top:1972px;width:210px;height:45px">Subscribe to Updates</a>

<div class="photo" role="img" aria-label="Three women embracing warmly in a sunlit golden field"></div>
<section class="subscribe">
  <h2 class="subscribe__title">Stay Connected</h2>
  <p class="subscribe__text">Receive inspiration, event updates, and ministry news directly to your inbox.</p>
  <div class="subscribe__input">Enter Email Address</div>
  <a class="btn btn--black subscribe__btn">Subcribe</a>
</section>

<footer>
  <a class="social" style="left:149px;top:2984px" aria-label="Social profile"><span class="social__mark"></span></a>
  <a class="social" style="left:199px;top:2984px" aria-label="Social profile"><span class="social__mark"></span></a>
  <a class="social" style="left:250px;top:2984px" aria-label="Video channel"><span class="social__mark"></span></a>
  <a class="social" style="left:300px;top:2984px" aria-label="Email"><svg width="18" height="14" viewBox="0 0 18 14"><rect width="18" height="14" rx="1.5" fill="#fff"/><path d="M1 1.5l8 6 8-6" fill="none" stroke="#07a69a" stroke-width="1.6"/></svg></a>
  <div class="abs brand" style="left:530px;top:2996px">
    <span class="brand__dot"></span>
    <span class="brand__name">Whole &amp;<br>Beloved</span>
  </div>
  <a class="btn btn--teal" style="left:930px;top:2984px;width:124px;height:44px">Donate Now</a>
  <nav class="nav" style="left:242px;top:3079px">
    <a>HOME</a><span class="sep">|</span><a>ABOUT US</a><span class="sep">|</span><a>MEETINGS &amp; EVENTS</a><span class="sep">|</span><a>LANTERNS BY THE RIVER</a><span class="sep">|</span><a>HEALING ROOMS</a><span class="sep">|</span><a>LIVE&nbsp; STREAMING</a>
  </nav>
  <div class="abs footer__rule"></div>
  <p class="abs copyright">Copyright@2025.All Rights Reserved.</p>
  <span class="abs pageno">C72</span>
</footer>

</body>
</html>
```